Web Calculator design Housing Investment

We have a web calculator that needs to be fixed from a design perspective. The key tasks are:<br/>1. Selecting icons / pictures / colours for the various steps<br/>2. Designing navigation between calculator steps<br/>3. Making suggestions for chart design. The limitation is that the charts are all using the Vextra API (the same charts that Vextra Grids use).<br/><br/>There are four entry screens and then a result screen. See attached PDF for screenshots. You can see our website at https://larkhollowfunds.com for our corporate colours and style.

Target Market(s)

Real Estate Investors

Industry/Entity Type

Financial Planning

Number of Pages Required

1 page

Font styles to use
Sans Serif
Other font styles liked:
• Ubuntu

Colors
86cae7
3176b5
0455a3
ffffff

Requirements
Must have
• New Icons
• Suggested design for navigation
• Suggested design for charts

```html
<!DOCTYPE html>
<html lang="en">
<head>
<meta charset="utf-8">
<title>Property Investment Calculator</title>
<link href="https://fonts.googleapis.com/css2?family=Ubuntu:wght@300;400;500;700&display=swap" rel="stylesheet">
<style>
:root{
  --page:#f3f6f8;
  --card:#ffffff;
  --navy:#0455a3;
  --mid:#3176b5;
  --sky:#86cae7;
  --map:#4db3f5;
  --ink:#3d3d3d;
  --muted:#7a7a7a;
  --line:#e6e6e6;
  --footer:#333333;
  --panel:#1e2227;
  --panel-2:#2a2f36;
}
*{box-sizing:border-box;margin:0;padding:0}
html,body{width:1200px;height:3196px;overflow:hidden}
body{background:var(--page);font-family:"Ubuntu",sans-serif;color:var(--ink);position:relative}
.step-card{position:absolute;left:93px;width:1014px;background:var(--card);box-shadow:0 2px 10px rgba(0,0,0,.06)}
.site-footer{position:absolute;left:0;right:0;bottom:0;height:50px;background:var(--footer);color:#cfcfcf;font-size:12px;display:flex;align-items:center;justify-content:center}
.site-footer b{color:var(--sky);font-weight:500;margin:0 3px}
.stepper{position:absolute;left:0;top:0;width:800px;height:100px}
.stepper-track{position:absolute;left:60px;width:693px;top:51px;height:2px;background:var(--line)}
.step{position:absolute;top:0;width:160px;margin-left:-80px;text-align:center}
.step-num{position:absolute;top:23px;left:0;right:0;font-size:14px;color:var(--muted)}
.step-dot{position:absolute;top:45px;left:73px;width:14px;height:14px;border-radius:50%;background:#e2e2e2}
.step-dot.done{background:#fff;border:1.5px solid var(--navy)}
.step-dot.done svg{position:absolute;left:2px;top:2px}
.step-dot.active{background:var(--navy)}
.step-label{position:absolute;top:72px;left:0;right:0;font-size:13px;color:var(--muted);white-space:nowrap}
.step.current .step-num,.step.current .step-label{color:var(--navy);font-weight:500}
.btn{position:absolute;top:34px;height:37px;border-radius:19px;font-size:15px;font-weight:700;display:flex;align-items:center;justify-content:center}
.btn-primary{background:var(--navy);color:#fff}
.btn-outline{border:2px solid var(--navy);color:var(--navy);background:#fff}
.question{position:absolute;left:0;right:0;text-align:center;font-size:28px;font-weight:300;color:var(--ink);line-height:35px}
.type-tile{position:absolute;top:235px;width:138px;height:152px;background:var(--navy);border:3px solid var(--navy)}
.type-tile .art{height:109px;background:linear-gradient(180deg,#ffffff,#dcebf6)}
.type-tile span{display:block;text-align:center;color:#fff;font-size:20px;line-height:37px}
.map-area{position:absolute;left:217px;top:232px;width:218px;height:205px;border-radius:40% 45% 40% 35%;background:linear-gradient(160deg,#bfe4fb,var(--map))}
.field-label{position:absolute;font-size:11px;color:var(--muted)}
.range{position:absolute;height:2px;background:#dadada}
.range i{position:absolute;left:0;top:0;height:2px;background:var(--navy)}
.range b{position:absolute;top:-4px;width:10px;height:10px;border-radius:50%;background:var(--navy)}
.range-value{position:absolute;font-size:11px;color:var(--muted)}
.method{position:absolute;top:222px;width:260px;margin-left:-130px;text-align:center}
.method svg{display:block;margin:0 auto}
.method h3{margin-top:16px;font-size:17px;font-weight:500;color:var(--ink)}
.method p{margin-top:8px;font-size:13px;line-height:17px;color:var(--muted)}
.forecast-title{position:absolute;left:0;right:0;top:130px;text-align:center;font-size:28px;font-weight:500;color:var(--ink)}
.form-label{position:absolute;right:510px;text-align:right;font-size:13px;line-height:18px;color:var(--muted)}
.select{position:absolute;left:515px;width:164px;height:35px;border:1px solid #c9d3dc;font-size:13px;color:var(--muted);display:flex;align-items:center;padding-left:10px}
.select em{position:absolute;right:-1px;top:-1px;width:35px;height:35px;background:var(--navy);display:flex;align-items:center;justify-content:center}
.chart-box{position:absolute;left:282px;top:305px;width:449px;height:147px;border:1px solid var(--line)}
.caption{position:absolute;left:282px;top:462px;font-size:11px;color:var(--muted)}
.calc-panel{position:absolute;left:22px;top:159px;width:968px;height:125px;background:var(--panel);color:#e8e8e8;font-size:7px}
.ctrl{position:absolute;right:0;text-align:right}
.mini-select{position:absolute;left:140px;width:130px;height:13px;background:#fff;color:#333;font-size:6px;padding:2px 4px;border-radius:2px}
.mini-range{position:absolute;left:140px;height:2px;background:#9ab}
.mini-range b{position:absolute;top:-3px;width:7px;height:7px;border-radius:50%;border:1px solid #8cf;background:var(--panel)}
.mini-chart{position:absolute;top:8px;height:110px;background:var(--panel-2)}
.summary{position:absolute;left:809px;top:0;width:159px;height:125px;text-align:center;font-size:8px;line-height:12px;padding-top:20px}
.summary strong{font-size:9px;font-weight:500;display:block}
.note{position:absolute;left:90px;right:40px;top:308px;text-align:center;font-size:11px;line-height:17px;color:var(--muted)}
</style>
</head>
<body>

<!-- Step 1 -->
<section class="step-card" style="top:72px;height:535px">
  <div class="stepper">
    <div class="stepper-track"></div>
    <div class="step current" style="left:60px"><div class="step-num">01</div><div class="step-dot active"></div><div class="step-label">Property Type</div></div>
    <div class="step" style="left:240px"><div class="step-num">02</div><div class="step-dot"></div><div class="step-label">Property Location</div></div>
    <div class="step" style="left:408px"><div class="step-num">03</div><div class="step-dot"></div><div class="step-label">Property Valuation</div></div>
    <div class="step" style="left:580px"><div class="step-num">04</div><div class="step-dot"></div><div class="step-label">Your Property Forecast</div></div>
    <div class="step" style="left:753px"><div class="step-num">05</div><div class="step-dot"></div><div class="step-label" style="top:74px">Calculation</div></div>
  </div>
  <div class="btn btn-primary" style="left:902px;width:93px">Next</div>
  <h2 class="question" style="top:142px">What type of property would<br>you like to compare?</h2>
  <div class="type-tile" style="left:364px"><div class="art" role="img" aria-label="Illustration of apartment buildings"></div><span>Unit</span></div>
  <div class="type-tile" style="left:509px"><div class="art" role="img" aria-label="Illustration of a house"></div><span>House</span></div>
  <footer class="site-footer">© 2019 <b>Larkhollow Funds</b>. All Right Reserved.</footer>
</section>

<!-- Step 2 -->
<section class="step-card" style="top:692px;height:535px">
  <div class="stepper">
    <div class="stepper-track"></div>
    <div class="step" style="left:60px"><div class="step-num">01</div><div class="step-dot done"><svg width="8" height="8" viewBox="0 0 8 8"><path d="M1 4l2 2 4-4" fill="none" stroke="#0455a3" stroke-width="1.3"/></svg></div><div class="step-label">Property Type</div></div>
    <div class="step current" style="left:240px"><div class="step-num">02</div><div class="step-dot active"></div><div class="step-label">Property Location</div></div>
    <div class="step" style="left:408px"><div class="step-num">03</div><div class="step-dot"></div><div class="step-label">Property Valuation</div></div>
    <div class="step" style="left:580px"><div class="step-num">04</div><div class="step-dot"></div><div class="step-label">Your Property Forecast</div></div>
    <div class="step" style="left:753px"><div class="step-num">05</div><div class="step-dot"></div><div class="step-label" style="top:74px">Calculation</div></div>
  </div>
  <div class="btn btn-outline" style="left:800px;width:96px">Privious</div>
  <div class="btn btn-primary" style="left:902px;width:93px">Next</div>
  <h2 class="question" style="top:142px">Where would this property be located?</h2>
  <div class="map-area" role="img" aria-label="Map of Australia with selectable states"></div>
  <div class="field-label" style="left:478px;top:253px">How much will the property cost? ⓘ</div>
  <div class="range" style="left:479px;top:283px;width:257px"><i style="width:43px"></i><b style="left:38px"></b></div>
  <div class="range-value" style="left:745px;top:277px">$ 500,000</div>
  <div class="field-label" style="left:478px;top:330px">How much will you invest? ⓘ</div>
  <div class="range" style="left:479px;top:360px;width:257px"><i style="width:21px"></i><b style="left:16px"></b></div>
  <div class="range-value" style="left:745px;top:354px">$ 200,000</div>
  <footer class="site-footer">© 2019 <b>Larkhollow Funds</b>. All Right Reserved.</footer>
</section>

<!-- Step 3 -->
<section class="step-card" style="top:1309px;height:534px">
  <div class="stepper">
    <div class="stepper-track"></div>
    <div class="step" style="left:60px"><div class="step-num">01</div><div class="step-dot done"><svg width="8" height="8" viewBox="0 0 8 8"><path d="M1 4l2 2 4-4" fill="none" stroke="#0455a3" stroke-width="1.3"/></svg></div><div class="step-label">Property Type</div></div>
    <div class="step" style="left:240px"><div class="step-num">02</div><div class="step-dot done"><svg width="8" height="8" viewBox="0 0 8 8"><path d="M1 4l2 2 4-4" fill="none" stroke="#0455a3" stroke-width="1.3"/></svg></div><div class="step-label">Property Location</div></div>
    <div class="step current" style="left:408px"><div class="step-num">03</div><div class="step-dot active"></div><div class="step-label">Property Valuation</div></div>
    <div class="step" style="left:580px"><div class="step-num">04</div><div class="step-dot"></div><div class="step-label">Your Property Forecast</div></div>
    <div class="step" style="left:753px"><div class="step-num">05</div><div class="step-dot"></div><div class="step-label" style="top:74px">Calculation</div></div>
  </div>
  <div class="btn btn-outline" style="left:800px;width:96px">Privious</div>
  <div class="btn btn-primary" style="left:902px;width:93px">Next</div>
  <h2 class="question" style="top:131px">How would you like to forecast the returns<br>from property?</h2>
  <div class="method" style="left:195px">
    <svg width="150" height="150" viewBox="0 0 150 150"><rect x="28" y="28" width="94" height="94" transform="rotate(45 75 75)" fill="#fff" stroke="#3176b5" stroke-width="1.2"/><rect x="36" y="36" width="78" height="78" transform="rotate(45 75 75)" fill="none" stroke="#86cae7" stroke-width="1"/><circle cx="75" cy="75" r="34" fill="#e7c46a" opacity=".55" role="img" aria-label="Calculator with coins and banknotes"/></svg>
    <h3>Relative Cost</h3><p>Use this to value property based on<br>mortgage cost relative to rent cost</p>
  </div>
  <div class="method" style="left:508px">
    <svg width="150" height="150" viewBox="0 0 150 150"><rect x="28" y="28" width="94" height="94" transform="rotate(45 75 75)" fill="#fff" stroke="#3176b5" stroke-width="1.2"/><rect x="36" y="36" width="78" height="78" transform="rotate(45 75 75)" fill="none" stroke="#86cae7" stroke-width="1"/><circle cx="75" cy="75" r="34" fill="#d9a84a" opacity=".45" role="img" aria-label="Hand passing a money bag"/></svg>
    <h3>Relative to Wages</h3><p>Use this to value property based on<br>mortgage cost relative to bages</p>
  </div>
  <div class="method" style="left:822px">
    <svg width="150" height="150" viewBox="0 0 150 150"><rect x="28" y="28" width="94" height="94" transform="rotate(45 75 75)" fill="#fff" stroke="#3176b5" stroke-width="1.2"/><rect x="36" y="36" width="78" height="78" transform="rotate(45 75 75)" fill="none" stroke="#86cae7" stroke-width="1"/><circle cx="63" cy="62" r="9" fill="none" stroke="#4db3f5" stroke-width="6"/><circle cx="87" cy="88" r="9" fill="none" stroke="#4db3f5" stroke-width="6"/><line x1="90" y1="56" x2="60" y2="94" stroke="#4db3f5" stroke-width="7" stroke-linecap="round"/></svg>
    <h3>Using Rental Yield</h3><p>Use this to value property based on<br>a rental yield</p>
  </div>
  <footer class="site-footer">© 2019 <b>Larkhollow Funds</b>. All Right Reserved.</footer>
</section>

<!-- Step 4 -->
<section class="step-card" style="top:1941px;height:594px">
  <div class="stepper">
    <div class="stepper-track"></div>
    <div class="step" style="left:60px"><div class="step-num">01</div><div class="step-dot done"><svg width="8" height="8" viewBox="0 0 8 8"><path d="M1 4l2 2 4-4" fill="none" stroke="#0455a3" stroke-width="1.3"/></svg></div><div class="step-label">Property Type</div></div>
    <div class="step" style="left:240px"><div class="step-num">02</div><div class="step-dot done"><svg width="8" height="8" viewBox="0 0 8 8"><path d="M1 4l2 2 4-4" fill="none" stroke="#0455a3" stroke-width="1.3"/></svg></div><div class="step-label">Property Location</div></div>
    <div class="step" style="left:408px"><div class="step-num">03</div><div class="step-dot done"><svg width="8" height="8" viewBox="0 0 8 8"><path d="M1 4l2 2 4-4" fill="none" stroke="#0455a3" stroke-width="1.3"/></svg></div><div class="step-label">Property Valuation</div></div>
    <div class="step current" style="left:580px"><div class="step-num">04</div><div class="step-dot active"></div><div class="step-label">Your Property Forecast</div></div>
    <div class="step" style="left:753px"><div class="step-num">05</div><div class="step-dot"></div><div class="step-label" style="top:74px">Calculation</div></div>
  </div>
  <div class="btn btn-outline" style="left:800px;width:96px">Privious</div>
  <div class="btn btn-primary" style="left:902px;width:93px">Next</div>
  <h2 class="forecast-title">Your Property price Forecast</h2>
  <div class="form-label" style="top:197px">Your have chosen to forecast property prices using</div>
  <div class="select" style="top:189px">Gross Tental Yield<em><svg width="9" height="6" viewBox="0 0 9 6"><path d="M1 1l3.5 3.5L8 1" fill="none" stroke="#fff" stroke-width="1.2"/></svg></em></div>
  <div class="form-label" style="top:240px">You can see how this ratio has charged over time (in blue)<br>below vs your asumption (in red) for</div>
  <div class="select" style="top:240px;padding-left:21px">Sydney House<em><svg width="9" height="6" viewBox="0 0 9 6"><path d="M1 1l3.5 3.5L8 1" fill="none" stroke="#fff" stroke-width="1.2"/></svg></em></div>
  <div class="chart-box">
    <svg width="449" height="147" viewBox="0 0 449 147" font-family="Ubuntu, sans-serif" font-size="7" fill="#8a8a8a">
      <line x1="170" y1="20" x2="186" y2="20" stroke="#3176b5" stroke-width="1.5"/><text x="189" y="22">Gross Rental Yield</text>
      <line x1="260" y1="20" x2="276" y2="20" stroke="#3176b5" stroke-width="1.5"/><text x="279" y="22">Forecast</text>
      <text x="15" y="30">15%</text><text x="15" y="60">10%</text><text x="18" y="90">5%</text><text x="18" y="120">0%</text>
      <g stroke="#eee"><line x1="34" y1="28" x2="440" y2="28"/><line x1="34" y1="58" x2="440" y2="58"/><line x1="34" y1="88" x2="440" y2="88"/><line x1="34" y1="118" x2="440" y2="118"/></g>
      <polyline fill="none" stroke="#4aa3e8" stroke-width="1.2" points="36,58 42,70 50,62 60,64 70,58 86,56 96,66 110,64 126,68 140,66 160,70 180,74 196,86 210,90 226,96 240,94 256,96 270,88 284,98 300,94 320,98 336,96 346,102 360,100 375,100"/>
      <line x1="375" y1="100" x2="440" y2="100" stroke="#3176b5" stroke-width="1.2"/>
      <g text-anchor="middle"><text x="75" y="132">1985</text><text x="116" y="132">1990</text><text x="156" y="132">1995</text><text x="196" y="132">2000</text><text x="236" y="132">2005</text><text x="276" y="132">2010</text><text x="316" y="132">2015</text><text x="356" y="132">2020</text><text x="396" y="132">2025</text></g>
    </svg>
  </div>
  <div class="caption">By default we assume the ratio stays at thelatest value of 3.4%.You can change this assumption using the slider.</div>
  <div class="range" style="left:282px;top:495px;width:451px"><i style="width:43px"></i><b style="left:38px"></b></div>
  <footer class="site-footer">© 2019 <b>Larkhollow Funds</b>. All Right Reserved.</footer>
</section>

<!-- Step 5 -->
<section class="step-card" style="top:2597px;height:576px">
  <div class="stepper">
    <div class="stepper-track"></div>
    <div class="step" style="left:60px"><div class="step-num">01</div><div class="step-dot done"><svg width="8" height="8" viewBox="0 0 8 8"><path d="M1 4l2 2 4-4" fill="none" stroke="#0455a3" stroke-width="1.3"/></svg></div><div class="step-label">Property Type</div></div>
    <div class="step" style="left:240px"><div class="step-num">02</div><div class="step-dot done"><svg width="8" height="8" viewBox="0 0 8 8"><path d="M1 4l2 2 4-4" fill="none" stroke="#0455a3" stroke-width="1.3"/></svg></div><div class="step-label">Property Location</div></div>
    <div class="step" style="left:408px"><div class="step-num">03</div><div class="step-dot done"><svg width="8" height="8" viewBox="0 0 8 8"><path d="M1 4l2 2 4-4" fill="none" stroke="#0455a3" stroke-width="1.3"/></svg></div><div class="step-label">Property Valuation</div></div>
    <div class="step" style="left:580px"><div class="step-num">04</div><div class="step-dot done"><svg width="8" height="8" viewBox="0 0 8 8"><path d="M1 4l2 2 4-4" fill="none" stroke="#0455a3" stroke-width="1.3"/></svg></div><div class="step-label">Your Property Forecast</div></div>
    <div class="step current" style="left:753px"><div class="step-num">05</div><div class="step-dot active"></div><div class="step-label" style="top:74px">Calculation</div></div>
  </div>
  <div class="btn btn-outline" style="left:790px;width:96px">Privious</div>
  <div class="btn btn-primary" style="left:895px;width:100px">Recalculate</div>
  <div class="calc-panel">
    <div style="position:absolute;left:0;top:0;width:313px;height:125px">
      <div class="ctrl" style="right:177px;top:13px">Choose Property:</div>
      <div class="mini-select" style="top:10px">Sydney House ⌄</div>
      <div class="ctrl" style="right:177px;top:40px">Choose Alternative Investment:</div>
      <div class="mini-select" style="top:37px">Global Shares ⌄</div>
      <div class="ctrl" style="right:177px;top:67px">How much will the property cost? ⓘ:</div>
      <div class="mini-range" style="top:70px;width:32px"><b style="left:28px"></b></div>
      <div style="position:absolute;left:282px;top:67px">$500,000</div>
      <div class="ctrl" style="right:177px;top:95px">How much will you invest? ⓘ:</div>
      <div class="mini-range" style="top:98px;width:14px"><b style="left:10px"></b></div>
      <div style="position:absolute;left:282px;top:95px">$200,000</div>
    </div>
    <div class="mini-chart" style="left:325px;width:230px">
      <svg width="230" height="110" viewBox="0 0 230 110" font-family="Ubuntu, sans-serif" font-size="5" fill="#aaa">
        <text x="8" y="22">200K</text><text x="8" y="45">100K</text><text x="12" y="68">0</text><text x="6" y="91">-100K</text>
        <line x1="28" y1="66" x2="222" y2="66" stroke="#556"/>
        <polyline fill="none" stroke="#3d8fe0" stroke-width="1" points="30,66 80,60 130,52 180,44 222,36"/>
        <polyline fill="none" stroke="#5a7fa8" stroke-width="1" points="30,66 80,66 130,64 180,58 222,50"/>
        <text x="62" y="56" fill="#3d8fe0">Shares</text><text x="160" y="42" fill="#3d8fe0">Property (+ no debt)</text>
        <g text-anchor="middle"><text x="38" y="103">2019</text><text x="74" y="103">2021</text><text x="110" y="103">2023</text><text x="146" y="103">2025</text><text x="182" y="103">2027</text><text x="216" y="103">2029</text></g>
      </svg>
    </div>
    <div class="mini-chart" style="left:568px;width:231px">
      <svg width="231" height="110" viewBox="0 0 231 110" font-family="Ubuntu, sans-serif" font-size="5" fill="#aaa">
        <rect x="70" y="6" width="8" height="4" fill="#3a5ee0"/><text x="81" y="10">Shares Cashflow</text>
        <rect x="128" y="6" width="8" height="4" fill="#5a6ee8"/><text x="139" y="10">Property Cashflow</text>
        <text x="10" y="26">10K</text><text x="14" y="50">0</text><text x="8" y="74">-10K</text><text x="8" y="94">-20K</text>
        <line x1="28" y1="48" x2="225" y2="48" stroke="#556"/>
        <g fill="#3a5ee0"><rect x="42" y="44" width="6" height="4"/><rect x="60" y="44" width="6" height="4"/><rect x="78" y="44" width="6" height="4"/><rect x="96" y="44" width="6" height="4"/><rect x="114" y="44" width="6" height="4"/><rect x="132" y="44" width="6" height="4"/><rect x="150" y="44" width="6" height="4"/><rect x="168" y="44" width="6" height="4"/><rect x="186" y="44" width="6" height="4"/><rect x="204" y="44" width="6" height="4"/></g>
        <g fill="#4a5fe6"><rect x="50" y="48" width="6" height="16"/><rect x="68" y="48" width="6" height="18"/><rect x="86" y="48" width="6" height="20"/><rect x="104" y="48" width="6" height="20"/><rect x="122" y="48" width="6" height="22"/><rect x="140" y="48" width="6" height="22"/><rect x="158" y="48" width="6" height="24"/><rect x="176" y="48" width="6" height="24"/><rect x="194" y="48" width="6" height="26"/><rect x="212" y="48" width="6" height="26"/></g>
        <g text-anchor="middle"><text x="40" y="103">2019</text><text x="76" y="103">2021</text><text x="112" y="103">2023</text><text x="148" y="103">2025</text><text x="184" y="103">2027</text><text x="218" y="103">2029</text></g>
      </svg>
    </div>
    <div class="summary">
      <strong>After 5 years:</strong>
      <div style="font-size:7px">Shares will return $82,431 more ⓘ</div>
      <strong style="margin-top:12px">After 10 years:</strong>
      <div style="font-size:7px">Shares will return $160,176 more ⓘ</div>
      <strong>Debt Contribution ⓘ</strong>
    </div>
  </div>
  <p class="note">Note: These are indicative figures based on a boad range of assumtion (below). Plese cotact Larkhollow Funds or a financial planner before makin any investment based on the assumtions from this calculato</p>
  <footer class="site-footer">© 2019 <b>Larkhollow Funds</b>. All Right Reserved.</footer>
</section>

</body>
</html>
```